Wholesale in Gold Jewellery & Gold Bullion

We are an established gold jewellery and gold bullion wholesaler selling these products to international clients. We already have a name and logo of our company, hence please view attached current card design. We need a completely new design to compliment our business and industry and the final design should be new and elegant.

Contact Information for Business Card

New card details must be same as per current card. Like logo, name, tel no. & etc.

Colors

Designer to choose colors to be used in the design.

```html
<!DOCTYPE html>
<html lang="en">
<head>
<meta charset="utf-8">
<title>Aurel &amp; Co – Business Card</title>
<link href="https://fonts.googleapis.com/css2?family=Bebas+Neue&family=Open+Sans:wght@400;600&display=swap" rel="stylesheet">
<style>
  :root {
    --backdrop: #151515;
    --card: #1f1f1f;
    --gold: #e9a514;
    --silver: #d4d4d4;
    --text-light: #c9c9c9;
    --rule: #4a4a4a;
  }
  * { box-sizing: border-box; margin: 0; padding: 0; }
  html, body {
    width: 1200px; height: 900px; overflow: hidden;
    background: var(--backdrop);
  }
  .canvas {
    width: 1200px; height: 900px;
    display: flex; flex-direction: column; align-items: center; justify-content: center;
    gap: 70px;
  }
  .card {
    width: 560px; height: 320px;
    background: var(--card);
    border-radius: 22px;
    position: relative;
    overflow: hidden;
    box-shadow: 0 14px 40px rgba(0,0,0,.55);
  }
  /* back side */
  .card-back { display: flex; align-items: center; justify-content: center; gap: 16px; }
  .mark-dot {
    width: 46px; height: 46px; border-radius: 50%;
    background: linear-gradient(135deg, #f2f2f2, #8f8f8f);
  }
  .back-name {
    font-family: "Bebas Neue", sans-serif;
    font-size: 52px; letter-spacing: 1px; color: var(--silver);
  }
  /* front side */
  .brand {
    position: absolute; top: 30px; left: 0; right: 0;
    display: flex; align-items: center; justify-content: center; gap: 16px;
  }
  .brand-dot { width: 40px; height: 40px; border-radius: 50%; background: var(--gold); }
  .brand-name {
    font-family: "Bebas Neue", sans-serif;
    font-size: 50px; letter-spacing: 1px; color: var(--gold); line-height: 1;
  }
  .brand-suffix {
    font-family: "Open Sans", sans-serif; font-weight: 600;
    font-size: 8px; color: var(--gold);
    writing-mode: vertical-rl; letter-spacing: 1px; margin-left: -10px;
  }
  .rule-top {
    position: absolute; top: 98px; left: 170px; right: 40px;
    height: 1px; background: var(--rule);
  }
  .rule-mid {
    position: absolute; top: 150px; left: 40px; right: 200px;
    height: 1px; background: var(--rule);
  }
  .person { position: absolute; left: 40px; top: 158px; }
  .person-name {
    font-family: "Bebas Neue", sans-serif;
    font-size: 26px; letter-spacing: .5px; color: var(--gold); line-height: 1;
  }
  .person-role {
    font-family: "Open Sans", sans-serif; font-size: 15px; color: var(--text-light);
    line-height: 20px; margin-bottom: 6px;
  }
  .contact-list { list-style: none; }
  .contact-list li {
    display: flex; align-items: center; gap: 10px;
    font-family: "Open Sans", sans-serif; font-size: 15px; color: var(--text-light);
    line-height: 20px;
  }
  .contact-list svg { width: 13px; height: 13px; fill: var(--gold); flex: none; }
  .address {
    position: absolute; right: 40px; top: 110px; text-align: right;
    font-family: "Open Sans", sans-serif; font-size: 15px; color: var(--text-light);
    line-height: 20px; font-style: normal;
  }
</style>
</head>
<body>
<main class="canvas">
  <section class="card card-back" aria-label="Card back">
    <span class="mark-dot"></span>
    <span class="back-name">Aurel &amp; Co</span>
  </section>

  <section class="card card-front" aria-label="Card front">
    <div class="brand">
      <span class="brand-dot"></span>
      <span class="brand-name">Aurel &amp; Co</span>
      <span class="brand-suffix">PTE LTD</span>
    </div>
    <div class="rule-top"></div>
    <div class="rule-mid"></div>

    <div class="person">
      <h1 class="person-name">Ravin Solanki</h1>
      <p class="person-role">Director</p>
      <ul class="contact-list">
        <li><svg viewBox="0 0 16 16"><path d="M3 1h3l1.5 4-2 1.2a9 9 0 0 0 4.3 4.3L11 8.5l4 1.5v3a2 2 0 0 1-2 2A13 13 0 0 1 1 3a2 2 0 0 1 2-2z"/></svg>+65 6100 2400</li>
        <li><svg viewBox="0 0 16 16"><path d="M4 0h8a1 1 0 0 1 1 1v14a1 1 0 0 1-1 1H4a1 1 0 0 1-1-1V1a1 1 0 0 1 1-1zm1 2v10h6V2zm3 11a1 1 0 1 0 0 2 1 1 0 0 0 0-2z"/></svg>+65 9100 5821</li>
        <li><svg viewBox="0 0 16 16"><path d="M4 0h8v5H4zM1 6h14a1 1 0 0 1 1 1v6h-3v3H3v-3H0V7a1 1 0 0 1 1-1zm4 6v3h6v-3z"/></svg>+65 6100 2411</li>
        <li><svg viewBox="0 0 16 16"><path d="M0 3h16v10H0zm1.5 1.2L8 9l6.5-4.8V4h-13z"/></svg>ravin@aurelco.com</li>
      </ul>
    </div>

    <address class="address">12 Marlow Lane<br>Singapore 208115</address>
  </section>
</main>
</body>
</html>
```